Marwick Law Letterhead

We need a new letterhead design for a Law Firm. The address for the law firm is 1475 Calloway Street, Suite 210, Houston, Texas 77041. Phone Number: 832-361-9027; Fax Number: 832-614-7359. The logo is uploaded to the project.

```html
<!DOCTYPE html>
<html lang="en">
<head>
<meta charset="utf-8">
<title>Marwick Law Letterhead</title>
<link href="https://fonts.googleapis.com/css2?family=Arimo:wght@400;700&family=Cinzel:wght@600&display=swap" rel="stylesheet">
<style>
  :root {
    --backdrop: #e9e9ea;
    --paper: #f7f7f7;
    --navy: #1f3266;
    --red: #c8192b;
    --ink: #2b2b2b;
    --muted: #6a6a6a;
  }
  * { margin: 0; padding: 0; box-sizing: border-box; }
  html, body { width: 1200px; height: 795px; overflow: hidden; }
  body {
    background: var(--backdrop);
    font-family: "Arimo", Arial, sans-serif;
    display: flex;
    align-items: center;
    justify-content: center;
  }
  .letterhead {
    position: relative;
    width: 562px;
    height: 795px;
    background: var(--paper);
    box-shadow: 0 2px 12px rgba(0,0,0,0.12);
  }
  .brand {
    position: absolute;
    top: 58px;
    left: 64px;
    display: flex;
    align-items: center;
    gap: 8px;
  }
  .brand-dot {
    width: 22px;
    height: 22px;
    border-radius: 50%;
    background: var(--navy);
  }
  .brand-text { display: flex; flex-direction: column; }
  .brand-name {
    font-family: "Arimo", Arial, sans-serif;
    font-weight: 700;
    font-size: 17px;
    color: var(--navy);
    letter-spacing: 0.3px;
    border-bottom: 1px solid var(--red);
    padding-bottom: 2px;
  }
  .brand-tagline {
    font-size: 4.5px;
    color: var(--red);
    letter-spacing: 0.6px;
    text-transform: uppercase;
    margin-top: 2px;
  }
  .letter {
    position: absolute;
    top: 250px;
    left: 64px;
    right: 56px;
    color: var(--ink);
  }
  .salutation { font-size: 11px; margin-bottom: 10px; }
  .letter p {
    font-size: 8.3px;
    line-height: 1.5;
    margin: 0 0 12px 14px;
    color: #3a3a3a;
  }
  .closing { font-size: 8.3px; margin: 6px 0 0 28px; color: #3a3a3a; }
  .signature {
    display: block;
    margin: 6px 0 0 46px;
    width: 80px;
    height: 28px;
    background: linear-gradient(90deg, rgba(30,30,30,0.15), rgba(30,30,30,0.05));
    border-radius: 3px;
  }
  .footer-band {
    position: absolute;
    left: 0;
    right: 0;
    bottom: 0;
    height: 26px;
    background: linear-gradient(90deg, var(--navy) 0%, #5a2763 55%, var(--red) 100%);
    display: flex;
    align-items: center;
    gap: 6px;
    padding-left: 64px;
    color: #fff;
    font-size: 8.2px;
    letter-spacing: 0.2px;
  }
  .footer-band svg { width: 8px; height: 8px; fill: #fff; flex: none; }
  .footer-item { display: flex; align-items: center; gap: 3px; }
</style>
</head>
<body>
  <main class="letterhead">
    <header class="brand">
      <span class="brand-dot"></span>
      <div class="brand-text">
        <span class="brand-name">Marwick Law</span>
        <span class="brand-tagline">Your trusted partner in legal matters</span>
      </div>
    </header>

    <section class="letter">
      <div class="salutation">Dear Mr. Harlan,</div>
      <p>Lorem ipsum dolor sit amet, consectetur adipiscing elit. Donec orci purus, luctus vitae dignissim eu, iaculis sed purus. Vivamus faucibus, ipsum nec aliquet viverra, leo mauris condimentum ligula, sit amet sagittis enim ligula quis arcu. Nam egestas tortor id nisi porttitor mattis. In tortor ante, ultricies in suscipit a, tempus non massa. Vivamus et auctor mi. Fusce vel massa nulla. Phasellus nec eros mauris, et scelerisque orci.</p>
      <p>Donec malesuada orci vitae nulla accumsan porta a id massa. Quisque accumsan iaculis magna sit amet fringilla. Maecenas consequat, magna eget tincidunt semper, odio nibh rutrum mi, id feugiat ante nisl eu risus. Vestibulum nunc orci, rhoncus a placerat in, ultricies in mi. Cras mattis varius eros, vel fringilla nisi suscipit eget. Quisque scelerisque sagittis nulla at porttitor.</p>
      <p>Sed id augue vitae urna euismod commodo aliquet a quam. Pellentesque arcu velit, cursus et malesuada ut, consequat et diam. Nullam erat sem, rhoncus id ullamcorper vitae, rhoncus et arcu. In ultricies ultricies nulla, ut rutrum nisl iaculis at. Donec eu magna a metus ornare faucibus. Fusce aliquet faucibus ultricies. Morbi semper, est id tincidunt gravida, sem arcu adipiscing lacus, ac bibendum nulla leo eu purus. Quisque nec diam sed risus consectetur accumsan quis quis nibh. Vestibulum id purus lorem.</p>
      <div class="closing">Sincerely,</div>
      <span class="signature" role="img" aria-label="Handwritten signature"></span>
    </section>

    <footer class="footer-band">
      <span class="footer-item">
        <svg viewBox="0 0 10 10" aria-hidden="true"><path d="M5 0a3.5 3.5 0 0 0-3.5 3.5C1.5 6 5 10 5 10s3.5-4 3.5-6.5A3.5 3.5 0 0 0 5 0zm0 5a1.5 1.5 0 1 1 0-3 1.5 1.5 0 0 1 0 3z"/></svg>
        1475 Calloway Street, Suite 210, Houston, Texas 77041
      </span>
      <span class="footer-item">
        <svg viewBox="0 0 10 10" aria-hidden="true"><path d="M2 0.5l2 2-1 1.3c.6 1.3 1.6 2.3 2.9 2.9l1.3-1 2 2-1.2 1.8C4.3 9.2.8 5.7.3 1.7z"/></svg>
        832-361-9027
      </span>
      <span class="footer-item">
        <svg viewBox="0 0 10 10" aria-hidden="true"><path d="M2.5 0h5v3h-5zM0.5 3.5h9v4h-2v2.5h-5V7.5h-2zM3.5 6.5v2.5h3V6.5z"/></svg>
        832-614-7359
      </span>
    </footer>
  </main>
</body>
</html>
```